Belvascotravel.com web design project + logo design

Hi,

We are a Russian online tour operator - sunkettle.com

We are looking to tranmsfer our domain to belvascotravel.com. The website and logo need to be belvascoesque - we are not looking to change our functionality, but we need to make the website much more attracitve to clients, much more wild looking but at the same time remaining a professional travel company.

The main concept of the website should be innovative travel (as belvasco was an innovator). Alternatively, you could go down the artist route and go down the draw / design your own tour road.

On our website the customer is able to combine travel services (hotels, flights, Visa services, and soon chauffeur, car rental etc...) put it into their basket (the basket definitely has to look better than it is at the moment) and pay for it in one go by card.

We are also stressin our customer support with web chat, call centre etc... (call centre number at the top of the page)

We aim to provide an easy user experience, but we need to make it have some more style, so I will be waiting for what you guys can come up with.
Let me know if you have any questions - skype is: mrdolbarin

Industry/Entity Type

It Company

Requirements
Must have
• It is quite a simple task - to take the existing website sunkettle.com and belvascosize it to create belvascotravel.com, the functionality of the website will remain the same and there are not many pages in the website. Homepage, Checkout step1, Checkout step 2 (you can view both of these if you select a service) and the generic pages for T&C''s, Privacy policy etc...

IMPORTANT UPDATE

We are also looking at how the search results will look in the designs, (please do a search on our website for hotel / flight)

```html
<!DOCTYPE html>
<html lang="en">
<head>
<meta charset="utf-8">
<title>Belvascotravel.com</title>
<link href="https://fonts.googleapis.com/css2?family=Open+Sans:wght@300;400;600;700&display=swap" rel="stylesheet">
<style>
:root{
  --blue:#1a8ad4;
  --navy:#1e5a9c;
  --logo:#1f3e8a;
  --panel-top:#0f3550;
  --panel-bottom:#1c5675;
  --green:#5aa33a;
  --text:#444;
  --muted:#999;
  --footer:#3d3d3d;
  --footer-bottom:#333;
  --footer-text:#7d7d7d;
}
*{margin:0;padding:0;box-sizing:border-box}
html,body{width:1200px;height:1152px;overflow:hidden}
body{position:relative;font-family:"Open Sans",Arial,sans-serif;color:var(--text);background:#fff}
.abs{position:absolute}
.topline{left:0;top:0;width:1200px;height:4px;background:var(--blue)}
.stage{left:0;top:108px;width:1200px;height:380px;background:linear-gradient(#e9e9e9,#fff)}
.brand{left:172px;top:58px;display:flex;align-items:center;gap:8px;font-weight:700;font-size:20px;color:var(--logo)}
.brand i{width:14px;height:14px;border-radius:50%;background:var(--green);display:block}
.phone{left:730px;top:11px;display:flex;align-items:center;gap:8px;font-size:17px;color:var(--muted)}
.login{left:885px;top:4px;width:187px;height:34px;background:var(--blue);border-radius:0 0 3px 3px;color:#fff;font-weight:700;font-size:13px;padding:8px 0 0 13px}
.login:after{content:"";position:absolute;right:9px;top:14px;border:4px solid transparent;border-top:6px solid #fff}
.nav{top:79px;font-weight:700;font-size:12px;color:var(--navy)}
.navline{left:367px;top:101px;width:711px;height:3px;background:#e4e4e4}
.navactive{left:500px;top:101px;width:46px;height:3px;background:var(--blue)}
.panel{left:126px;top:108px}
.lbl{color:#fff;font-weight:700;font-size:14px}
.field{background:#fff;border-radius:3px;font-size:11px;font-style:italic;color:#888;padding:7px 0 0 11px;height:29px}
.cal{position:absolute;right:11px;top:7px;width:18px;height:14px;border:2px solid #46b4c8;border-radius:2px}
.sel-div{position:absolute;right:30px;top:4px;width:1px;height:21px;background:#ddd}
.sel-div:after{content:"";position:absolute;left:12px;top:9px;border:4px solid transparent;border-top:5px solid var(--blue)}
.proceed{left:142px;top:412px;width:92px;height:31px;background:var(--green);border-radius:3px;color:#fff;font-size:14px;font-weight:600;text-align:center;line-height:31px}
.hero{left:356px;top:108px;width:723px;height:347px;background:linear-gradient(#4f8fd6 0%,#a9c9ea 38%,#6d9ac4 48%,#d8c49c 55%,#c9ae80 100%);box-shadow:0 2px 6px rgba(0,0,0,.35)}
.social{left:147px;display:flex;align-items:center;gap:12px;font-size:13px;color:#555}
.social i{width:32px;height:32px;border-radius:50%;display:block}
.card{top:507px;width:221px;height:195px;border-top:2px solid #e2e2e2;background:linear-gradient(#f1f1f1,#fff);padding:12px 11px}
.card h3{font-size:15px;font-weight:600;color:#222;display:flex;align-items:center;gap:7px;margin-bottom:12px}
.card p{font-size:11px;line-height:19px;color:#555}
.card a{display:block;margin-top:6px;font-size:12px;font-weight:600;color:var(--blue)}
.sec-title{left:132px;top:700px;font-size:19px;font-weight:300;color:#555}
.sec-line{left:256px;top:710px;width:811px;height:1px;background:#ddd}
.tile{top:737px;width:221px;height:194px;background:#f0f0f0}
.tile .img{height:154px}
.tile span{display:block;text-align:center;font-size:15px;color:#555;padding-top:10px}
.tile.active{border-bottom:3px solid var(--green)}
.footer{left:0;top:978px;width:1200px;height:132px;background:var(--footer)}
.notch{left:590px;top:978px;border:8px solid transparent;border-top:9px solid #fff}
.fnav{top:1019px;font-size:11px;color:var(--footer-text)}
.fline{top:1042px;height:1px;background:#4d4d4d}
.frow{top:1055px;display:flex;align-items:center;gap:10px;font-size:11px;color:#8a8a8a}
.ficon{top:1054px;width:16px;height:16px;border-radius:50%;background:#6a6a6a}
.bottom{left:0;top:1110px;width:1200px;height:42px;background:var(--footer-bottom);font-size:11px;color:#8a8a8a}
.bottom span{position:absolute;top:15px}
.sep{position:absolute;top:12px;width:1px;height:18px;background:#4a4a4a}
</style>
</head>
<body>
<div class="abs stage"></div>
<div class="abs topline"></div>

<div class="abs brand"><i></i>belvascotravel.com</div>

<div class="abs phone">
  <svg width="16" height="16" viewBox="0 0 24 24"><path fill="#aaa" d="M6.6 10.8a15 15 0 006.6 6.6l2.2-2.2c.3-.3.7-.4 1-.2 1.1.4 2.3.6 3.6.6.6 0 1 .4 1 1V20c0 .6-.4 1-1 1A17 17 0 013 4c0-.6.4-1 1-1h3.5c.6 0 1 .4 1 1 0 1.3.2 2.5.6 3.6.1.3 0 .7-.2 1z"/></svg>
  00-31-480-480
</div>
<div class="abs login">Login to Your Account</div>

<nav>
  <span class="abs nav" style="left:503px">HOME</span>
  <span class="abs nav" style="left:585px">DESTINATIONS</span>
  <span class="abs nav" style="left:718px">ACTIVITIES</span>
  <span class="abs nav" style="left:826px">TRIP STYLES</span>
  <span class="abs nav" style="left:942px">RESPONSIBLE TRAVEL</span>
</nav>
<div class="abs navline"></div>
<div class="abs navactive"></div>

<svg class="abs panel" width="230" height="377" viewBox="0 0 230 377">
  <defs><linearGradient id="pg" x1="0" y1="0" x2="0" y2="1"><stop offset="0" stop-color="#0f3550"/><stop offset="1" stop-color="#1c5675"/></linearGradient></defs>
  <polygon points="0,0 230,0 230,356 118,376 0,356" fill="url(#pg)"/>
  <line x1="18" y1="16" x2="212" y2="16" stroke="#2a6583" stroke-width="1"/>
</svg>

<div class="abs lbl" style="left:144px;top:143px">Find a Place</div>
<div class="abs field" style="left:143px;top:168px;width:198px">Enter Destination...</div>
<div class="abs lbl" style="left:146px;top:205px">Check In</div>
<div class="abs field" style="left:143px;top:230px;width:167px">DD/MM/YY<i class="cal"></i></div>
<div class="abs lbl" style="left:145px;top:272px">Check Out</div>
<div class="abs field" style="left:143px;top:297px;width:157px">DD/MM/YY<i class="cal"></i></div>
<div class="abs lbl" style="left:144px;top:338px">Guests</div>
<div class="abs field" style="left:143px;top:363px;width:127px">06<i class="sel-div"></i></div>
<div class="abs proceed">Proceed</div>

<div class="abs hero" role="img" aria-label="Photo of a thatched wooden shade on a sandy beach by a calm sea under a blue sky"></div>

<div class="abs social" style="top:523px"><i style="background:#3b5998"></i>find us on facepage</div>
<div class="abs social" style="top:565px"><i style="background:#2aa3e0"></i>find us on chirpline</div>
<div class="abs social" style="top:608px"><i style="background:#333"></i>find us on circleplus</div>

<div class="abs card" style="left:367px">
  <h3><svg width="16" height="14" viewBox="0 0 16 14"><path d="M9 1l6 5-6 5V8C5 8 3 9 1 13c0-5 3-8 8-8z" fill="#1c4a66"/></svg>Visa Services</h3>
  <p>Le Lorem Ipsum est simplement du faux texte employé dans la composition et la mise en page avant impression. Le Lorem Ipsum est le faux texte standard</p>
  <a href="#">Read More</a>
</div>
<div class="abs card" style="left:608px">
  <h3><span style="font-weight:700;color:#1c4a66;width:14px;text-align:center">?</span>Flight Services</h3>
  <p>Le Lorem Ipsum est simplement du faux texte employé dans la composition et la mise en page avant impression. Le Lorem Ipsum est le faux texte standard</p>
  <a href="#">Read More</a>
</div>
<div class="abs card" style="left:848px">
  <h3><svg width="16" height="14" viewBox="0 0 16 14"><path d="M8 0l8 7h-2v7h-4V9H6v5H2V7H0z" fill="#1c4a66"/></svg>Hotel Services</h3>
  <p>Le Lorem Ipsum est simplement du faux texte employé dans la composition et la mise en page avant impression. Le Lorem Ipsum est le faux texte standard</p>
  <a href="#">Read More</a>
</div>

<div class="abs sec-title">Our Services</div>
<div class="abs sec-line"></div>

<div class="abs tile" style="left:132px"><div class="img" role="img" aria-label="Beach umbrella and two loungers on white sand by turquoise sea" style="background:linear-gradient(#2f7fc9,#6fc3e0 50%,#eee6d2 62%,#d9cdb3)"></div><span>Visa Services</span></div>
<div class="abs tile active" style="left:372px"><div class="img" role="img" aria-label="Wooden pier with a small hut over dark teal water" style="background:linear-gradient(#16323f,#1d5a63 45%,#1a6b6c)"></div><span>Flight Services</span></div>
<div class="abs tile" style="left:609px"><div class="img" role="img" aria-label="Wooden chair on a lakeside deck with mountains and flowers" style="background:linear-gradient(#3a86d2,#a7cde6 30%,#6c8f7a 48%,#7ea7a2 65%,#b5703a)"></div><span>Hotel Services</span></div>
<div class="abs tile" style="left:847px"><div class="img" role="img" aria-label="Thatched shade on a sandy beach by the sea" style="background:linear-gradient(#4a8fd6,#a9c9ea 42%,#6d9ac4 50%,#d8c49c 58%,#c9ae80)"></div><span>Other Services</span></div>

<div class="abs footer"></div>
<div class="abs notch"></div>

<span class="abs fnav" style="left:130px">Home</span>
<span class="abs fnav" style="left:199px">Destinations</span>
<span class="abs fnav" style="left:303px">Activities</span>
<span class="abs fnav" style="left:389px">Trip Styles</span>
<span class="abs fnav" style="left:481px">Responsible Travel</span>
<span class="abs fnav" style="left:849px;top:1015px">STAY CONNECTED</span>
<div class="abs fline" style="left:130px;width:699px"></div>
<div class="abs fline" style="left:849px;width:220px"></div>

<div class="abs frow" style="left:130px">
  <svg width="16" height="14" viewBox="0 0 16 14"><path d="M8 0l8 7h-2v7h-4V9H6v5H2V7H0z" fill="#777"/></svg>Lorem Ipsum is simply dummy text of the printinge
</div>
<div class="abs frow" style="left:465px">
  <svg width="14" height="14" viewBox="0 0 24 24"><path fill="#777" d="M6.6 10.8a15 15 0 006.6 6.6l2.2-2.2c.3-.3.7-.4 1-.2 1.1.4 2.3.6 3.6.6.6 0 1 .4 1 1V20c0 .6-.4 1-1 1A17 17 0 013 4c0-.6.4-1 1-1h3.5c.6 0 1 .4 1 1 0 1.3.2 2.5.6 3.6.1.3 0 .7-.2 1z"/></svg>(123) 456-7890
</div>
<div class="abs frow" style="left:595px">
  <svg width="15" height="11" viewBox="0 0 15 11"><rect x=".5" y=".5" width="14" height="10" fill="none" stroke="#777"/><path d="M.5.5l7 5 7-5" fill="none" stroke="#777"/></svg>contact@companyname.com
</div>

<i class="abs ficon" style="left:849px"></i>
<i class="abs ficon" style="left:884px;border-radius:2px"></i>
<i class="abs ficon" style="left:919px"></i>
<i class="abs ficon" style="left:955px"></i>
<i class="abs ficon" style="left:989px"></i>
<i class="abs ficon" style="left:1024px;border-radius:2px"></i>

<div class="abs bottom">
  <span style="left:130px">Belvasco Travel © 2013</span>
  <i class="sep" style="left:254px"></i>
  <span style="left:270px">Legal Notice</span>
  <i class="sep" style="left:353px"></i>
  <span style="left:369px">Terms</span>
</div>
</body>
</html>
```